Website Design for The Elder Nook

Please design and code a new website.
Here are the sites I like best:
http://www.voyaglint.com/alternate/
http://www.wheelgiftbay.org
Please make it similar but look at the competitor site (below) for images and wording. This is NOT a car donation site. It's a senior lead placement site like https://www.kinhavenfinder.com. I just like this sites above as a lead generation sites.
Competitor site:
https://www.kinhavenfinder.com (use ideas / verbiage from this site)
Updates
Competitor site:
Coding
Coded - Design and coding required
Number of Pages Required
1 page
Look and feel
Each slider illustrates characteristics of the customer's brand and the style your logo design should communicate.

```html
<!DOCTYPE html>
<html lang="en">
<head>
<meta charset="utf-8">
<title>The Elder Nook – Senior Living Advisors</title>
<link href="https://fonts.googleapis.com/css2?family=Montserrat:wght@400;600;700;800&family=Open+Sans:wght@400;600;700&display=swap" rel="stylesheet">
<style>
:root{
  --navy:#0f3557;
  --navy-dark:#0a2640;
  --green:#5d9a83;
  --tan:#d6b27c;
  --orange:#f0b554;
  --ink:#1d2b3a;
  --muted:#5c6670;
  --line:#c9ced4;
  --grey:#dedede;
  --white:#ffffff;
}
*{box-sizing:border-box;margin:0;padding:0}
html,body{width:1200px;height:3810px;overflow:hidden}
body{font-family:"Open Sans",Arial,sans-serif;color:var(--ink);background:var(--white)}
.heading{font-family:"Montserrat",Arial,sans-serif;font-weight:700;color:var(--navy);text-transform:uppercase;letter-spacing:.5px}
section,header,footer{position:relative;width:1200px;overflow:hidden}

/* Header */
.topbar{height:70px;background:var(--navy);display:flex;align-items:center;justify-content:space-between;padding:0 40px}
.brand{font-family:"Montserrat",sans-serif;font-weight:700;font-size:30px;color:var(--white)}
.social{display:flex;gap:8px;align-items:center;color:var(--white);font-size:12px}
.social span.sq{width:18px;height:18px;background:var(--white);opacity:.85;display:block}
.mainnav{height:50px;background:var(--navy-dark);display:flex;align-items:center;gap:34px;padding:0 40px;border-top:1px solid rgba(255,255,255,.15)}
.mainnav a{font-family:"Montserrat",sans-serif;font-weight:700;font-size:13px;color:var(--white);text-decoration:none;text-transform:uppercase}

/* Hero */
.hero{height:413px;background:linear-gradient(120deg,#8a9f6a 0%,#b8c49a 35%,#6f8a74 70%,#4f6e5e 100%)}
.hero-photo{position:absolute;inset:0}
.lead-form{position:absolute;left:700px;top:0;width:330px;height:413px;background:rgba(93,154,131,.93);padding:22px 26px;color:var(--white)}
.call-row{display:flex;gap:12px;align-items:center;margin-bottom:16px}
.call-row .ring{width:48px;height:48px;border:2px solid var(--white);border-radius:50%;display:flex;align-items:center;justify-content:center;flex:none}
.call-row b{display:block;font-family:"Montserrat",sans-serif;font-size:14px;white-space:nowrap}
.call-row strong{display:block;font-family:"Montserrat",sans-serif;font-size:24px;line-height:1.1;white-space:nowrap}
.call-row small{font-size:11px;white-space:nowrap}
.lead-form .field{background:var(--white);height:28px;margin-bottom:8px;font-size:11px;color:#777;padding:6px 8px}
.lead-form .field.area{height:70px}
.btn{display:inline-block;font-family:"Montserrat",sans-serif;font-weight:700;font-size:12px;text-transform:uppercase;background:var(--navy);color:var(--white);padding:10px 22px}
.lead-form .btn{margin:6px 0 0 0}

/* Why choose us */
.why{height:172px;background:var(--tan)}
.why-label{position:absolute;left:0;top:0;height:172px;width:270px;background:var(--green);clip-path:polygon(0 0,100% 0,82% 100%,0 100%);display:flex;align-items:center;padding-left:30px}
.why-label h2{font-family:"Montserrat",sans-serif;font-weight:800;font-size:34px;line-height:1.05;color:var(--white)}
.why-list{position:absolute;left:300px;top:0;height:172px;width:880px;display:flex;justify-content:space-around;align-items:center}
.why-item{width:140px;text-align:center;font-size:12px;color:var(--ink);line-height:1.35}
.why-item svg{display:block;margin:0 auto 10px}

/* How it works */
.how{height:470px;padding-top:70px}
.rule-title{display:flex;align-items:center;justify-content:center;gap:30px}
.rule-title::before,.rule-title::after{content:"";width:200px;height:2px;background:var(--line)}
.rule-title h2{font-size:24px}
.steps{display:flex;justify-content:center;gap:60px;margin-top:70px}
.step{width:210px;text-align:center}
.step h3{font-family:"Montserrat",sans-serif;font-weight:700;font-size:15px;color:var(--navy);margin:18px 0 14px;line-height:1.35}
.step p{font-size:12px;color:var(--muted);line-height:1.55;text-align:left}

/* Spokesperson */
.spokes{height:333px;background:linear-gradient(100deg,#2f4e6c 0%,#3a5d7a 40%,#5a6f7c 70%,#2c4058 100%)}
.spokes::after{content:"";position:absolute;inset:0;background:rgba(15,53,87,.55)}
.spokes-card{position:absolute;z-index:2;left:40px;top:135px;width:400px;height:175px;background:var(--white);border-radius:12px;padding:36px 34px 0;text-align:center}
.avatar{position:absolute;z-index:3;left:205px;top:55px;width:120px;height:120px;border-radius:50%;background:linear-gradient(#c9a58a,#8f6b58);border:5px solid var(--white)}
.spokes-card h3{font-family:"Montserrat",sans-serif;font-size:16px;color:var(--navy);margin-bottom:10px}
.spokes-card p{font-size:11px;color:var(--muted);line-height:1.5}
.no-cost{position:absolute;z-index:2;left:790px;top:175px;font-family:"Montserrat",sans-serif;font-weight:700;white-space:nowrap}
.no-cost span{display:block;color:var(--white);font-size:20px;margin-bottom:4px}
.no-cost strong{display:block;color:var(--orange);font-size:28px}

/* FAQ */
.faq{height:524px;padding-top:70px}
.faq h2{text-align:center;font-size:24px}
.faq-body{display:flex;gap:40px;margin:60px 0 0 28px}
.aid-card{position:relative;width:520px;height:360px;background:var(--tan)}
.aid-photo{position:absolute;right:0;top:0;width:260px;height:360px;background:linear-gradient(#9a8a72,#5e5242)}
.aid-text{position:absolute;left:40px;top:90px;color:var(--white);font-family:"Montserrat",sans-serif;font-weight:800}
.aid-text span{display:block;font-size:22px}
.aid-text strong{display:block;font-size:56px;line-height:1.05}
.aid-text em{display:block;font-style:normal;font-size:24px;line-height:1.2}
.aid-card .btn{position:absolute;left:110px;top:300px}
.accordion{width:570px}
.acc-item{border:1px solid var(--line);border-radius:4px;height:36px;margin-bottom:14px;display:flex;justify-content:space-between;align-items:center;padding:0 16px;font-family:"Montserrat",sans-serif;font-weight:700;font-size:13px;color:var(--ink)}
.acc-item.open{height:auto;display:block;padding:10px 16px 14px}
.acc-item.open .acc-head{display:flex;justify-content:space-between;margin-bottom:8px}
.acc-item.open p{font-family:"Open Sans",sans-serif;font-weight:400;font-size:12px;color:var(--muted);line-height:1.5}

/* Advisor */
.advisor{height:333px;background:linear-gradient(100deg,#243c4e 0%,#3f5a64 45%,#2d4a5a 100%);text-align:center;padding-top:110px}
.advisor::after{content:"";position:absolute;inset:0;background:rgba(15,53,87,.5)}
.advisor-inner{position:relative;z-index:2}
.advisor h2{font-family:"Montserrat",sans-serif;font-weight:700;font-size:28px;color:var(--tan)}
.advisor p{color:var(--white);font-size:14px;margin:6px 0 18px}
.advisor .field{width:310px;height:28px;background:var(--white);margin:0 auto 8px;font-size:12px;color:#777;text-align:left;padding:5px 10px}
.advisor .btn{background:var(--tan);color:var(--navy);width:310px}

/* States */
.states{height:525px;padding-top:80px}
.states h2{text-align:center;font-size:24px}
.tabs{display:flex;justify-content:center;gap:20px;margin:40px 0 44px}
.tabs span{font-family:"Montserrat",sans-serif;font-size:14px;color:var(--muted);padding:6px 16px}
.tabs span.active{background:#e3e7ec;color:var(--navy);font-weight:700;border-bottom:3px solid var(--navy)}
.state-cols{display:flex;margin-left:40px}
.state-cols ul{list-style:none;width:272px}
.state-cols li{font-size:13px;font-weight:700;color:var(--navy);line-height:19px}

/* Testimonials */
.reviews{height:540px;background:var(--grey);text-align:center;padding-top:100px}
.reviews h2{font-size:28px;line-height:1.2}
.faces{display:flex;justify-content:center;gap:28px;margin:40px 0 55px}
.faces span{width:110px;height:110px;border-radius:50%;border:5px solid var(--white)}
.reviews blockquote{width:840px;margin:0 auto;font-size:15px;font-weight:700;line-height:1.5;color:var(--ink)}
.reviews cite{display:block;font-style:normal;font-size:13px;color:var(--muted);margin:14px 0 20px}

/* Footer */
.site-footer{height:348px;background:var(--navy);color:var(--white)}
.footer-wave{position:absolute;left:0;top:0}
.footer-brand{position:absolute;left:0;right:0;top:14px;text-align:center;font-family:"Montserrat",sans-serif;font-weight:700;font-size:34px}
.footer-col{position:absolute;top:150px}
.footer-col h4{font-family:"Montserrat",sans-serif;font-size:13px;font-weight:700;padding-bottom:10px;border-bottom:1px solid rgba(255,255,255,.4);margin-bottom:16px;width:300px}
.footer-col p{font-size:12px;line-height:1.6;width:300px;font-weight:600}
.footer-col ul{list-style:none}
.footer-col li{font-family:"Montserrat",sans-serif;font-size:11px;font-weight:700;line-height:20px}
.footer-call{position:absolute;left:780px;top:210px;width:370px;height:100px;border:2px solid var(--white);border-radius:12px;display:flex;align-items:center;gap:16px;padding:0 22px}
.footer-call svg{flex:none}
.footer-call b{display:block;font-family:"Montserrat",sans-serif;font-size:15px;white-space:nowrap;line-height:1.3}
.footer-call strong{display:block;font-family:"Montserrat",sans-serif;font-size:26px;line-height:1.2;white-space:nowrap}
.footer-call small{display:block;font-size:12px;white-space:nowrap;line-height:1.4}
.copyright{height:32px;background:var(--navy-dark);color:var(--white);font-size:12px;text-align:center;line-height:32px}
</style>
</head>
<body>

<header>
  <div class="topbar">
    <div class="brand">The Elder Nook</div>
    <div class="social"><span class="sq"></span><span class="sq"></span><span class="sq"></span><span>&nbsp;Eng ▾</span></div>
  </div>
  <nav class="mainnav">
    <a href="#">Assisted Living</a><a href="#">Memory Care</a><a href="#">Nursing Homes</a><a href="#">More Living Options</a><a href="#">Planning &amp; Advice</a><a href="#">How Our Service Works</a>
  </nav>
</header>

<section class="hero">
  <div class="hero-photo" role="img" aria-label="Photo of an older man hugging his grown son outdoors among trees"></div>
  <form class="lead-form">
    <div class="call-row">
      <div class="ring"><svg width="24" height="24" viewBox="0 0 24 24"><path d="M6.6 10.8a15 15 0 0 0 6.6 6.6l2.2-2.2a1 1 0 0 1 1-.25 11.4 11.4 0 0 0 3.6.57 1 1 0 0 1 1 1V20a1 1 0 0 1-1 1A17 17 0 0 1 3 4a1 1 0 0 1 1-1h3.5a1 1 0 0 1 1 1c0 1.25.2 2.45.57 3.6a1 1 0 0 1-.25 1z" fill="#fff"/></svg></div>
      <div><b>NEED HELP? CALL NOW</b><strong>0-000-000-0000</strong><small>Find Senior Living Near You</small></div>
    </div>
    <div class="field">First Name</div>
    <div class="field">Last Name</div>
    <div class="field">Email</div>
    <div class="field">Zip Code</div>
    <div class="field area">Messages</div>
    <span class="btn">Submit</span>
  </form>
</section>

<section class="why">
  <div class="why-label"><h2>WHY<br>CHOOSE US</h2></div>
  <div class="why-list">
    <div class="why-item"><svg width="40" height="40" viewBox="0 0 40 40"><circle cx="20" cy="12" r="7" fill="#0f3557"/><path d="M6 36c0-8 6-13 14-13s14 5 14 13z" fill="#0f3557"/></svg>Dedicated local advisor</div>
    <div class="why-item"><svg width="40" height="40" viewBox="0 0 40 40"><rect x="8" y="4" width="24" height="32" rx="2" fill="none" stroke="#0f3557" stroke-width="3"/><path d="M13 13h14M13 20h14M13 27h9" stroke="#0f3557" stroke-width="3"/></svg>Hand-picked list of communities to match your needs</div>
    <div class="why-item"><svg width="40" height="40" viewBox="0 0 40 40"><rect x="4" y="12" width="32" height="20" rx="3" fill="#0f3557"/><circle cx="20" cy="22" r="5" fill="#d6b27c"/></svg>Full details and pricing</div>
    <div class="why-item"><svg width="40" height="40" viewBox="0 0 40 40"><rect x="5" y="8" width="30" height="28" rx="2" fill="none" stroke="#0f3557" stroke-width="3"/><path d="M5 15h30M12 4v8M28 4v8" stroke="#0f3557" stroke-width="3"/></svg>Help scheduling tours</div>
    <div class="why-item"><svg width="40" height="40" viewBox="0 0 40 40"><path d="M6 26l4-10h20l4 10v6H6z" fill="#0f3557"/><circle cx="12" cy="32" r="3" fill="#d6b27c"/><circle cx="28" cy="32" r="3" fill="#d6b27c"/></svg>Move in support</div>
  </div>
</section>

<section class="how">
  <div class="rule-title"><h2 class="heading">How Our Service Works</h2></div>
  <div class="steps">
    <div class="step">
      <svg width="56" height="56" viewBox="0 0 56 56"><circle cx="16" cy="14" r="7" fill="#5d9a83"/><circle cx="40" cy="14" r="7" fill="#5d9a83"/><path d="M6 40c0-9 4-15 10-15s10 6 10 15zM30 40c0-9 4-15 10-15s10 6 10 15z" fill="#5d9a83"/><rect x="14" y="42" width="28" height="4" fill="#5d9a83"/></svg>
      <h3>Talk with your local<br>advisor</h3>
      <p>A local advisor listens to your needs, explains costs and care types, and guides your family at every step.</p>
    </div>
    <div class="step">
      <svg width="56" height="56" viewBox="0 0 56 56"><circle cx="28" cy="12" r="8" fill="#5d9a83"/><path d="M14 50V30c0-6 6-9 14-9s14 3 14 9v20z" fill="#5d9a83"/></svg>
      <h3>Get informative on<br>care options</h3>
      <p>A local advisor listens to your needs, explains costs and care types, and guides your family at every step.</p>
    </div>
    <div class="step">
      <svg width="56" height="56" viewBox="0 0 56 56"><circle cx="14" cy="14" r="6" fill="#5d9a83"/><circle cx="28" cy="10" r="6" fill="#5d9a83"/><circle cx="42" cy="14" r="6" fill="#5d9a83"/><path d="M4 48V30c0-5 4-8 10-8s10 3 10 8v18zM32 48V30c0-5 4-8 10-8s10 3 10 8v18zM19 44V24c0-5 4-7 9-7s9 2 9 7v20z" fill="#5d9a83"/></svg>
      <h3>Choose communities<br>to visit</h3>
      <p>A local advisor listens to your needs, explains costs and care types, and guides your family at every step.</p>
    </div>
    <div class="step">
      <svg width="56" height="56" viewBox="0 0 56 56"><rect x="22" y="8" width="26" height="42" fill="#5d9a83"/><path d="M27 14h6M37 14h6M27 22h6M37 22h6M27 30h6M37 30h6" stroke="#fff" stroke-width="3"/><path d="M12 30a8 8 0 1 0-0.1 0zM12 44l-7-12h14z" fill="#5d9a83"/><circle cx="12" cy="24" r="3" fill="#fff"/></svg>
      <h3>Transition to new<br>home</h3>
      <p>A local advisor listens to your needs, explains costs and care types, and guides your family at every step.</p>
    </div>
  </div>
</section>

<section class="spokes" role="img" aria-label="Photo of seniors relaxing together in a bright living room">
  <div class="avatar" role="img" aria-label="Portrait of the spokesperson"></div>
  <div class="spokes-card">
    <h3>Marla J. - The Elder Nook<br>spokesperson</h3>
    <p>Our team has helped thousands of families find the right senior living home. We talk with you, learn what matters most, and share trusted local options at no cost to your family, ever.</p>
  </div>
  <div class="no-cost"><span>There's no cost to you</span><strong>Call: 0-000-000-0000</strong></div>
</section>

<section class="faq">
  <h2 class="heading">Frequently Asked Questions</h2>
  <div class="faq-body">
    <div class="aid-card">
      <div class="aid-photo" role="img" aria-label="Photo of an elderly veteran in a suit standing on steps"></div>
      <div class="aid-text"><span>Accessup to</span><strong>$2,000</strong><em>per month in<br>veteran's aid</em></div>
      <span class="btn">Learn More</span>
    </div>
    <div class="accordion">
      <div class="acc-item open"><div class="acc-head"><span>Lorem Ipsum is simply dummy text</span><span>⌄</span></div>
        <p>Many families can get help paying for care. Our advisors explain benefits, eligibility rules and the steps to apply, so you know exactly where to begin.</p></div>
      <div class="acc-item"><span>Lorem Ipsum is simply dummy text</span><span>⌄</span></div>
      <div class="acc-item"><span>Lorem Ipsum is simply dummy text</span><span>⌄</span></div>
      <div class="acc-item"><span>Lorem Ipsum is simply dummy text</span><span>⌄</span></div>
      <div class="acc-item"><span>Lorem Ipsum is simply dummy text</span><span>⌄</span></div>
      <div class="acc-item"><span>Lorem Ipsum is simply dummy text</span><span>⌄</span></div>
    </div>
  </div>
</section>

<section class="advisor" role="img" aria-label="Photo of a quiet tree-lined residential street">
  <div class="advisor-inner">
    <h2>FIND YOUR LOCAL ADVISOR</h2>
    <p>Lorem Ipsum is simply dummy text of the printing and typesetting industry</p>
    <div class="field">Enter your city or postal code</div>
    <span class="btn">Find Advisor</span>
  </div>
</section>

<section class="states">
  <h2 class="heading">Senior Living by State</h2>
  <div class="tabs"><span>Assisted Living</span><span class="active">Memory Care</span><span>Independent Living</span><span>Nursing Home</span><span>Care Homes</span></div>
  <div class="state-cols">
    <ul><li>Alabama</li><li>Alaska</li><li>Arkansas</li><li>California</li><li>Colorado</li><li>Connecticut</li><li>Delaware</li><li>District of Columbia</li><li>Florida</li><li>Georgia</li><li>Hawaii</li><li>Idaho</li><li>Illinois</li><li>Indiana</li></ul>
    <ul><li>Iowa</li><li>Kansas</li><li>Kentucky</li><li>Louisiana</li><li>Maine</li><li>Maryland</li><li>Massachusetts</li><li>Michigan</li><li>Minnesota</li><li>Mississippi</li><li>Missouri</li><li>Montana</li><li>Nebraska</li><li>Nevada</li></ul>
    <ul><li>New Hampshire</li><li>New Jersey</li><li>New Mexico</li><li>New York</li><li>North Carolina</li><li>North Dakota</li><li>Ohio</li><li>Oklahoma</li><li>Oregon</li><li>Pennsylvania</li><li>Rhode Island</li><li>South Carolina</li><li>South Dakota</li><li>Tennessee</li></ul>
    <ul><li>Texas</li><li>Utah</li><li>Vermont</li><li>Virginia</li><li>Washington</li><li>West Virginia</li><li>Wisconsin</li><li>Wyoming</li></ul>
  </div>
</section>

<section class="reviews">
  <h2 class="heading">82% of our customers<br>recommend our service</h2>
  <div class="faces">
    <span role="img" aria-label="Customer portrait" style="background:#b9c3cc"></span>
    <span role="img" aria-label="Customer portrait" style="background:#7d6a5c"></span>
    <span role="img" aria-label="Customer portrait" style="background:#e4e4e4"></span>
    <span role="img" aria-label="Customer portrait" style="background:#d8c4b0"></span>
  </div>
  <blockquote>There are many variations of passages of Lorem Ipsum available, but the majority have suffered alteration in some form, by injected humour, or randomised words which don't look even slightly believable</blockquote>
  <cite>Ted R., CA</cite>
  <span class="btn">View More</span>
</section>

<footer class="site-footer">
  <svg class="footer-wave" width="1200" height="60" viewBox="0 0 1200 60"><path d="M0 0H1200V50H900C850 50 840 0 790 0H410C360 0 350 50 300 50H0Z" fill="#dedede"/></svg>
  <div class="footer-brand">The Elder Nook</div>
  <div class="footer-col" style="left:40px">
    <h4>ABOUT US</h4>
    <p>The Elder Nook is a free senior living referral service that connects families with trusted communities and local advisors across the country.</p>
  </div>
  <div class="footer-col" style="left:430px">
    <h4>LINKS</h4>
    <ul><li>ASSISTED LIVING</li><li>MEMORY CARE</li><li>NURSING HOMES</li><li>MORE LIVING OPTIONS</li><li>PLANNING &amp; ADVICE</li><li>HOW OUR SERVICE WORKS</li></ul>
  </div>
  <div class="footer-call">
    <svg width="46" height="46" viewBox="0 0 24 24"><circle cx="12" cy="12" r="11" fill="none" stroke="#fff" stroke-width="1.5"/><path d="M8.3 10.6a8 8 0 0 0 3.9 3.9l1.3-1.3a.6.6 0 0 1 .6-.15 6.7 6.7 0 0 0 2.1.34.6.6 0 0 1 .6.6V16a.6.6 0 0 1-.6.6A10 10 0 0 1 6.4 6.6.6.6 0 0 1 7 6h2.1a.6.6 0 0 1 .6.6c0 .74.12 1.45.34 2.1a.6.6 0 0 1-.15.6z" fill="#fff"/></svg>
    <div><b>NEED HELP? CALL NOW</b><strong>0-000-000-0000</strong><small>Find Senior Living Near You</small></div>
  </div>
</footer>
<div class="copyright">© copyright The Elder Nook 2019</div>

</body>
</html>
```